Oil Field Service company needs professional business cards

Looking to clean up our current company business cards and look a little more professional. Brenwick Casing Services is a US based company that services the oil field. We deal with engineers, managers and oil rigs....................................................................................................................................................................................................................................................................................................................................................................................................

Target Market(s)

Oil and Gas professionals

Industry/Entity Type

Oil And Gas

Contact Information for Business Card

See attached photo as example

Font styles to use
Sans Serif

Colors
ec1f27

Requirements
Must have
• Company Logo, Name, Title, Cell, Office, Fax, Email.
• See attached photo
Nice to have
• External CRT, Internal CRT, Casing Crews, Torque Turn, Laydown Machine
Should not have
• Do not introduce any new pictures and keep it professional looking

```html
<!DOCTYPE html>
<html lang="en">
<head>
<meta charset="utf-8">
<title>Brenwick Casing Services – Business Cards</title>
<link href="https://fonts.googleapis.com/css2?family=Roboto:wght@400;500;700&display=swap" rel="stylesheet">
<style>
  :root {
    --brand-red: #d8232a;
    --brand-navy: #3d5366;
    --ink: #3a3f44;
    --card: #f7f7f7;
    --backdrop: #e4e4e4;
    --white: #ffffff;
  }
  * { box-sizing: border-box; margin: 0; padding: 0; }
  html, body { width: 1200px; height: 576px; overflow: hidden; }
  body {
    background: var(--backdrop);
    font-family: "Roboto", Arial, sans-serif;
    position: relative;
  }
  .card {
    position: absolute;
    background: var(--card);
    border-radius: 6px;
    box-shadow: 0 2px 5px rgba(0,0,0,.25);
    overflow: hidden;
  }
  .card--front { left: 82px; top: 139px; width: 485px; height: 293px; }
  .card--back  { left: 602px; top: 138px; width: 481px; height: 292px; }

  .wordmark { position: absolute; text-align: center; color: var(--brand-navy); font-weight: 700; }
  .wordmark__name { display: block; letter-spacing: 1px; line-height: 1; }
  .wordmark__sub { display: block; letter-spacing: 2.4px; line-height: 1; }

  .card--front .wordmark { left: 0; width: 100%; top: 92px; }
  .card--front .wordmark__name { font-size: 44px; }
  .card--front .wordmark__sub { font-size: 17px; margin-top: 14px; }

  .service-band {
    position: absolute; left: 0; top: 220px; width: 100%; height: 27px;
    background: var(--brand-red); color: var(--white);
    font-size: 13px; font-weight: 700; letter-spacing: .2px;
    display: flex; align-items: center; justify-content: center; gap: 6px;
  }
  .web-line {
    position: absolute; left: 0; width: 100%; top: 262px;
    display: flex; align-items: center; justify-content: center; gap: 10px;
    font-size: 13px; color: var(--ink);
  }

  .back-art { position: absolute; left: 0; top: 0; }
  .service-list {
    position: absolute; right: 26px; top: 18px; list-style: none;
    text-align: right; color: var(--white); font-size: 12.5px; font-weight: 700; line-height: 18px;
  }
  .card--back .wordmark { left: 26px; top: 108px; width: 250px; }
  .card--back .wordmark__name { font-size: 38px; }
  .card--back .wordmark__sub { font-size: 15px; margin-top: 14px; }

  .contact { position: absolute; list-style: none; font-size: 11.5px; color: var(--ink); line-height: 16px; }
  .contact li { display: flex; align-items: center; gap: 7px; }
  .contact svg { width: 10px; height: 10px; fill: var(--brand-red); flex: none; }
  .contact--phones { left: 30px; top: 221px; }
  .contact--details { left: 250px; top: 221px; }
</style>
</head>
<body>

<section class="card card--front" aria-label="Business card front">
  <div class="wordmark">
    <span class="wordmark__name">BRENWICK</span>
    <span class="wordmark__sub">CASING SERVICES</span>
  </div>
  <div class="service-band">
    <span>LAYDOWN MACHINE</span><span>|</span><span>CASING CREW</span><span>|</span><span>MUD TOOL</span><span>|</span><span>TORQUE TURN</span>
  </div>
  <div class="web-line">
    <svg width="70" height="4" viewBox="0 0 70 4"><path d="M0 2 L70 0 L70 4 Z" fill="var(--brand-red)"/></svg>
    <span>www.brenwickcs.com</span>
    <svg width="70" height="4" viewBox="0 0 70 4"><path d="M70 2 L0 0 L0 4 Z" fill="var(--brand-red)"/></svg>
  </div>
</section>

<section class="card card--back" aria-label="Business card back">
  <svg class="back-art" width="481" height="292" viewBox="0 0 481 292">
    <path d="M0 0 H481 V118 C400 120 330 50 230 30 C150 14 60 18 0 36 Z" fill="var(--brand-red)"/>
    <path d="M0 50 C70 20 170 14 250 38 C330 62 390 128 481 132 V140 C390 136 320 80 240 56 C160 34 70 40 0 64 Z" fill="var(--brand-navy)"/>
  </svg>
  <ul class="service-list">
    <li>Laydown Machine &nbsp;«</li>
    <li>Casing Crew &nbsp;«</li>
    <li>Torque Turn &nbsp;«</li>
    <li>Mud Tool &nbsp;«</li>
  </ul>
  <div class="wordmark">
    <span class="wordmark__name">BRENWICK</span>
    <span class="wordmark__sub">CASING SERVICES</span>
  </div>
  <ul class="contact contact--phones">
    <li><svg viewBox="0 0 10 10"><path d="M2 0 L4 2 L3 3.5 C4 5 5 6 6.5 7 L8 6 L10 8 L8.5 10 C4 9 1 6 0 1.5 Z"/></svg>(555) 014-5700</li>
    <li><svg viewBox="0 0 10 10"><path d="M0 3 C2 1 8 1 10 3 L10 4.5 L7.5 4.5 L7 3.5 H3 L2.5 4.5 H0 Z M2 5 H8 L9 10 H1 Z"/></svg>(555) 014-7496</li>
    <li><svg viewBox="0 0 10 10"><path d="M2.5 0 H7.5 V3 H2.5 Z M0 3.5 H10 V8 H8 V6 H2 V8 H0 Z M2.5 6.5 H7.5 V10 H2.5 Z"/></svg>(555) 014-3230</li>
  </ul>
  <ul class="contact contact--details">
    <li><svg viewBox="0 0 10 10"><path d="M5 0 C7.5 0 9 1.8 9 3.8 C9 6.5 5 10 5 10 C5 10 1 6.5 1 3.8 C1 1.8 2.5 0 5 0 Z M5 2.3 A1.5 1.5 0 1 0 5 5.3 A1.5 1.5 0 1 0 5 2.3 Z"/></svg>Cedarline, OK 73899</li>
    <li><svg viewBox="0 0 10 10"><path d="M0 1.5 H10 L5 5.5 Z M0 3 L5 7 L10 3 V8.5 H0 Z"/></svg>jwalden@brenwickcs.com</li>
    <li><svg viewBox="0 0 10 10"><circle cx="5" cy="5" r="4.2" fill="none" stroke="var(--brand-red)" stroke-width="1.2"/><path d="M0.8 5 H9.2 M5 0.8 C3 3 3 7 5 9.2 M5 0.8 C7 3 7 7 5 9.2" fill="none" stroke="var(--brand-red)" stroke-width="0.9"/></svg>www.brenwickcs.com</li>
  </ul>
</section>

</body>
</html>
```